Web Design Project - Shipping Industry

Goals and Objectives
The objective of the new website is to create a more modern look and feel. The site will also allow for a more effective means of communicating with members while providing the public with information and developments in the local, regional and international shipping industry.
Scope
The website will highlight the history of the organisation inclusive of text and photographs. It will take visitors through the years from beginning to present. Information on the history of the shipping industry will also be included.
It will feature current articles on the organisation, its members and stakeholders in the shipping industry. Member information as well as pertinent details regarding the organisation’s subsidiaries will be documented for the website.
Information as it relates to shipping statistics, case studies, laws and regulations, international treaties and trade documents, shipping terms, careers in shipping, job opportunities, training opportunities, information for shippers including port listing and trade lanes will be main features of the content for the website.
The Association’s community involvement, industry calendar events and related links relevant industry members will also be featured.
Target Market
• The General Public;
• Members of the organization;
• Shipping Industry Stakeholders (local, regional and international);
• Tertiary students conducting research.
• Potential employees
• Potential Business Partners
Best Practice Bench Marketing
The following websites are being looked at:
• Korvel Quayworks - http://www.korvelquayworks.example/ (preferred look)
• Tessaly Maritime Association - http://www.tma-freight.example/ (like image transition on main page)
• Drovna - http://www.drovna.example (professional look)
• PLW - http://www.pelworth.example (preferred color: blue in logo)
• Quillo - http://www.quillo.example/electronics/tv-video-audio/ (preferred look for links page: image + short text below + visit site link)
Expected Result
• 3 - 5 pages which must include: [1] main page [2] standard page [3] links page

```html
<!DOCTYPE html>
<html lang="en">
<head>
<meta charset="utf-8">
<title>Halvern PCS – Global Shipper</title>
<link href="https://fonts.googleapis.com/css2?family=Oswald:wght@500;600&family=Arimo:wght@400;700&display=swap" rel="stylesheet">
<style>
  :root {
    --navy: #0b2a57;
    --navy-deep: #032457;
    --navy-light: #16457f;
    --ink: #1a1a1a;
    --grey-logo: #d3d6db;
    --grey-icon: #9a9da1;
    --panel: #eef0f3;
    --white: #ffffff;
  }
  * { box-sizing: border-box; margin: 0; padding: 0; }
  html, body { width: 886px; height: 1200px; overflow: hidden; background: var(--white); }
  body { position: relative; font-family: "Arimo", Arial, sans-serif; color: var(--ink); }
  a { color: inherit; text-decoration: none; }

  .brand { position: absolute; left: 26px; top: 30px; font-family: "Oswald", sans-serif; font-weight: 600; font-size: 38px; color: var(--navy); letter-spacing: .5px; }
  .locate { position: absolute; left: 688px; top: 37px; display: flex; align-items: center; gap: 16px; font-size: 12px; color: var(--navy-deep); }
  .locate-map { width: 62px; height: 40px; border-radius: 4px; background: radial-gradient(ellipse, #b9d8ee, #e4f0f8 75%); }

  .main-nav { position: absolute; left: 16px; top: 104px; width: 852px; height: 47px; background: linear-gradient(#1a4c8a, var(--navy-deep)); border: 1px solid #0a2148; display: flex; align-items: center; }
  .main-nav a { color: var(--white); font-weight: 700; font-size: 12px; height: 100%; display: flex; align-items: center; padding: 0 17px 0 16px; border-right: 1px solid #0a1e40; box-shadow: 1px 0 0 #2d5d98; }
  .search { position: absolute; right: 12px; top: 11px; width: 158px; height: 22px; border-radius: 4px; background: var(--white); }
  .search svg { position: absolute; right: 8px; top: 4px; }

  .hero { position: absolute; left: 16px; top: 158px; width: 852px; height: 368px; }
  .hero-photo { position: absolute; inset: 0; background: linear-gradient(#c3ccd6 0%, #dde3ea 35%, #8fb8cf 52%, #4a5f70 70%, #2f4050 100%); }
  .hero-caption { position: absolute; left: 0; bottom: 0; width: 100%; height: 98px; background: rgba(10, 40, 88, .88); color: var(--white); padding: 12px 26px; }
  .hero-caption h1 { font-family: "Oswald", sans-serif; font-weight: 500; font-size: 24px; letter-spacing: .5px; line-height: 30px; }
  .hero-caption p { font-size: 12px; line-height: 18px; margin-top: 5px; width: 760px; }
  .hero-next { position: absolute; right: 20px; top: 18px; }

  .feature { position: absolute; top: 554px; width: 263px; }
  .feature h2 { height: 44px; background: linear-gradient(var(--white), var(--panel)); border-bottom: 2px solid var(--navy); font-family: "Oswald", sans-serif; font-weight: 600; font-size: 24px; color: var(--navy); padding: 4px 12px; letter-spacing: .3px; }
  .feature-photo { margin-top: 10px; height: 136px; }
  .photo-ship { background: linear-gradient(#556270 0%, #8a97a5 40%, #2c56b5 70%, #11306a 100%); }
  .photo-port { background: linear-gradient(#3b3f6d 0%, #b06a5a 38%, #d9a24a 60%, #1e2a44 100%); }
  .feature p { font-size: 12px; line-height: 18.2px; padding: 5px 4px 0; }
  .btn { position: absolute; top: 328px; left: 3px; width: 98px; height: 29px; background: linear-gradient(var(--navy-light), var(--navy-deep)); color: var(--white); font-size: 12px; display: flex; align-items: center; justify-content: center; }
  .feature.services .btn, .feature.advantages .btn { left: 0; }

  .footer-rule { position: absolute; left: 21px; top: 957px; width: 852px; height: 4px; background: var(--navy); }
  .footer-links { position: absolute; top: 996px; list-style: none; font-size: 11.5px; line-height: 20px; color: var(--navy-deep); }
  .footer-brand { position: absolute; left: 551px; top: 992px; font-family: "Oswald", sans-serif; font-weight: 600; font-size: 24px; color: var(--grey-logo); }
  .footer-contact { position: absolute; left: 552px; top: 1033px; font-size: 10px; line-height: 16px; color: var(--navy-deep); }
  .social { position: absolute; left: 546px; top: 1105px; display: flex; gap: 15px; }
  .social span { width: 30px; height: 30px; border-radius: 50%; background: radial-gradient(circle at 40% 35%, #c5c7ca, var(--grey-icon)); }
  .legal { position: absolute; left: 13px; top: 1158px; width: 860px; height: 27px; background: var(--navy); color: var(--white); font-size: 10px; padding: 7px 9px; }
</style>
</head>
<body>
  <header>
    <div class="brand">Halvern PCS</div>
    <a class="locate" href="#"><span class="locate-map" role="img" aria-label="Dotted world map"></span>Locate Us</a>
  </header>

  <nav class="main-nav">
    <a href="#">Home</a><a href="#">About Us</a><a href="#">Sustainability</a><a href="#">News</a><a href="#">Careers</a><a href="#">Links</a><a href="#">Contact Us</a>
    <div class="search">
      <svg width="14" height="14" viewBox="0 0 14 14"><circle cx="5.5" cy="5.5" r="4.2" fill="none" stroke="#bbb" stroke-width="1.6"/><line x1="8.6" y1="8.6" x2="12.5" y2="12.5" stroke="#bbb" stroke-width="1.8"/></svg>
    </div>
  </nav>

  <section class="hero">
    <div class="hero-photo" role="img" aria-label="Container ship sailing on open sea under a cloudy sky"></div>
    <div class="hero-caption">
      <h1>GLOBAL SHIPPER</h1>
      <p>Lorem ipsum dolor sit amet, consectetuer adipiscing elit, sed diam nonummy nibh euismod tincidunt ut laoreet dolore magna aliquam erat volutpat. Ut wisi enim ad minim veniam, quis nostrud exerci tation ullamcorper suscipit lobortis nisl ut aliquip ex ea commodo consequat.</p>
      <svg class="hero-next" width="40" height="62" viewBox="0 0 40 62"><polygon points="2,2 18,2 38,31 18,60 2,60 22,31" fill="#6f86a6" opacity=".8"/></svg>
    </div>
  </section>

  <article class="feature about" style="left:17px">
    <h2>ABOUT US</h2>
    <div class="feature-photo photo-ship" role="img" aria-label="Loaded container ship at sea"></div>
    <p>Lorem ipsum dolor sit amet, consectetuer adipi-scing elit, sed diam nonummy nibh euismod tincid-unt ut laoreet dolore magna aliquam erat volutpat. Ut wisi enim ad minim veniam, quis nostrud exerci tation ullamcorper suscipit lobortis nisl ut aliquip ex ea commodo consequat.</p>
    <a class="btn" href="#">Read More</a>
  </article>

  <article class="feature services" style="left:311px">
    <h2>OUR SERVICES</h2>
    <div class="feature-photo photo-port" role="img" aria-label="Port cranes lit at dusk"></div>
    <p style="padding-left:0">Lorem ipsum dolor sit amet, consectetuer adipi-scing elit, sed diam nonummy nibh euismod tincid-unt ut laoreet dolore magna aliquam erat volutpat. Ut wisi enim ad minim veniam, quis nostrud exerci tation ullamcorper suscipit lobortis nisl ut aliquip ex ea commodo consequat.</p>
    <a class="btn" href="#">Read More</a>
  </article>

  <article class="feature advantages" style="left:604px">
    <h2>OUR ADVANTAGES</h2>
    <div class="feature-photo photo-ship" role="img" aria-label="Loaded container ship at sea"></div>
    <p style="padding-left:0">Lorem ipsum dolor sit amet, consectetuer adipiscing elit, sed diam nonummy nibh euismod tincidunt ut laoreet dolore magna aliquam erat volutpat. Ut wisi enim ad minim veniam, quis nostrud exerci tation ullamcorper suscipit lobortis nisl ut aliquip ex ea commodo consequat.</p>
    <a class="btn" href="#">Read More</a>
  </article>

  <footer>
    <div class="footer-rule"></div>
    <ul class="footer-links" style="left:21px">
      <li>Home</li><li>About Us</li><li>Sustainability</li><li>News</li><li>nvestors Relations</li><li>Press Releases</li>
    </ul>
    <ul class="footer-links" style="left:161px">
      <li>Investors Relations</li><li>Press Releases</li><li>Terms and Conditions</li><li>Privacy Policy</li><li>Careers</li><li>Links</li><li>Contact Us</li>
    </ul>
    <ul class="footer-links" style="left:329px">
      <li>Investors Relations</li><li>Press Releases</li><li>Terms and Conditions</li><li>Privacy Policy</li><li>Careers</li><li>Links</li><li>Contact Us</li>
    </ul>
    <div class="footer-brand">Halvern PCS</div>
    <div class="footer-contact">xxxx-xxxxx-xxxxxxxxxxxxx<br>xxxx-xxxxx-xxxxxxx<br>xxxx-xxxxx-xxxxxxxxxxxxx</div>
    <div class="social"><span></span><span></span><span></span><span></span></div>
    <div class="legal">Copyrights Reserved 2012 @ Halvern PCS</div>
  </footer>
</body>
</html>
```